Form With Marla - Health and Wellness Business Card and Logo

I need a business card design with a logo for my business you can check out at www.formwithmarla.net. I want something more original, simplistic, and memorable than the basic logo I have on my site currently. I am a health and wellness coach and I offer mindset coaching and nutrition plans. I like the colour teal and dark grey/black for my theme colours. I emphasize growth, longterm change, and the whole package of "healthy mind, healthy body, healthy life". I had played around the idea of intertwining 3 M's or incorporating growth (leaves etc.) into my design. I want my expertise and experience to show through. In one glance I want people to understand with confidence I can help them accomplish anything they set their minds to. I look forward to seeing what everyone comes up with!

Industry/Entity Type

Health And Wellness

Contact Information for Business Card

Form With Marla
Marla Prentiss
BSc, Health & Wellness Coach
"Manifest your best"
www.formwithmarla.net
formwithmarla@quillpost.net
472-618-9043

Colors
33b8a4
ffffff
333333
000000

Requirements
Must have
• A memorable and unique logo for my business!
Nice to have
• Could have the phrase "Are you unhappy with your body and state of health?" or "It takes the right skills to develop habits in order to create long term change. I can help you get there."

```html
<!DOCTYPE html>
<html lang="en">
<head>
<meta charset="utf-8">
<title>Form With Marla – Business Card</title>
<link rel="stylesheet" href="https://fonts.googleapis.com/css2?family=Questrial&family=Open+Sans:wght@400;700&display=swap">
<style>
  :root {
    --backdrop: #2b2b2b;
    --card-black: #1c1c1c;
    --card-black-edge: #262626;
    --teal-light: #14a39c;
    --teal-deep: #067a74;
    --white: #ffffff;
    --mark-grey: #7a7a7a;
  }
  * { margin: 0; padding: 0; box-sizing: border-box; }
  html, body { width: 1200px; height: 1000px; overflow: hidden; }
  body {
    background: var(--backdrop);
    position: relative;
    font-family: "Open Sans", Arial, sans-serif;
  }
  .card {
    position: absolute;
    left: 250px;
    width: 700px;
    height: 400px;
    overflow: hidden;
    box-shadow: 0 14px 30px rgba(0,0,0,.45);
  }
  /* Front: black */
  .card-front {
    top: 50px;
    background: linear-gradient(160deg, var(--card-black-edge), var(--card-black));
  }
  .brand-mark {
    position: absolute;
    top: 140px;
    left: 0; right: 0;
    text-align: center;
    font-family: "Questrial", Arial, sans-serif;
    font-size: 44px;
    color: var(--mark-grey);
  }
  .tagline {
    position: absolute;
    bottom: 48px;
    left: 0; right: 0;
    text-align: center;
    font-size: 16px;
    letter-spacing: 5px;
    color: var(--white);
  }
  /* Back: teal */
  .card-back {
    top: 520px;
    background: radial-gradient(circle at 55% 45%, var(--teal-light), var(--teal-deep) 75%);
    color: var(--white);
  }
  .business-name {
    position: absolute;
    top: 36px;
    left: 80px;
    font-family: "Questrial", Arial, sans-serif;
    font-size: 46px;
  }
  .name-tab {
    position: absolute;
    top: 120px;
    left: 0;
    width: 14px;
    height: 40px;
    background: var(--white);
    border-radius: 0 6px 6px 0;
  }
  .person-name {
    position: absolute;
    top: 114px;
    left: 38px;
    font-size: 28px;
    font-weight: 700;
    letter-spacing: .5px;
  }
  .person-title {
    position: absolute;
    top: 152px;
    left: 38px;
    font-size: 15px;
    font-weight: 700;
  }
  .contact-list {
    position: absolute;
    top: 222px;
    left: 40px;
    list-style: none;
  }
  .contact-list li {
    display: flex;
    align-items: center;
    gap: 14px;
    font-size: 18px;
    line-height: 28px;
  }
  .contact-list svg { width: 14px; height: 14px; flex: none; }
  .corner-mark {
    position: absolute;
    right: 36px;
    bottom: 34px;
    font-size: 22px;
    font-weight: 700;
    color: var(--white);
  }
</style>
</head>
<body>
  <section class="card card-front">
    <div class="brand-mark">Form With Marla</div>
    <p class="tagline">"Manifest your best"</p>
  </section>

  <section class="card card-back">
    <h1 class="business-name">Form With Marla</h1>
    <span class="name-tab"></span>
    <h2 class="person-name">MARLA PRENTISS</h2>
    <p class="person-title">BSc, Health &amp; Wellness Coach</p>
    <ul class="contact-list">
      <li>
        <svg viewBox="0 0 16 16" aria-hidden="true"><path fill="#fff" d="M3.6 1l2.3 2.9-1.3 1.7c.9 2 2.6 3.7 4.6 4.6l1.7-1.3L13.8 11l-1.4 2.9C7 14 2 9 2.1 3.5z"/></svg>
        472-618-9043
      </li>
      <li>
        <svg viewBox="0 0 16 16" aria-hidden="true"><rect x="1" y="3" width="14" height="10" fill="#fff"/><path d="M1 3l7 6 7-6" fill="none" stroke="#0b8a84" stroke-width="1.3"/></svg>
        formwithmarla@quillpost.net
      </li>
      <li>
        <svg viewBox="0 0 16 16" aria-hidden="true"><g fill="none" stroke="#fff" stroke-width="1.3"><circle cx="8" cy="8" r="6.5"/><ellipse cx="8" cy="8" rx="3" ry="6.5"/><path d="M1.5 8h13M2.5 5h11M2.5 11h11"/></g></svg>
        www.<b>formwithmarla</b>.net
      </li>
      <li>
        <svg viewBox="0 0 16 16" aria-hidden="true"><circle cx="8" cy="8" r="6.5" fill="#fff"/></svg>
        @marlaprentiss
      </li>
    </ul>
    <div class="corner-mark">Form With Marla</div>
  </section>
</body>
</html>
```